New Business Card for Web Design/Internet Marketing Company

Looking for a great looking new business card. We are a 10 year old web design, internet marketing and website management company that works mostly with small businesses.

Our new card needs to better match the colors and style of our website, be bold, extremely usable and slightly edgy.

Target Market(s)

Small/Medium businesses that have websites

Industry/Entity Type

Internet

Requirements
Must have
• Front and back design, full color, rounded corners please

Must use the colors/style of our website (JPG provided)

INFO FOR CARDS (as readable as possible please)
Mark Lenner
President/CEO
mark@trelvanmedia.example
Phone: 520-381-7459
Toll Free: 866-381-7459
Address: 4315 W. Calloway Ave. Ste. 140, Tucson, AZ 85792

THINGS I WANT TO PROMOTE (if there is room):
1. Our Website - www.trelvanmedia.example

2. Social Media
Twitter: @trelvanmedia
Facebook: www.facebook.com/trelvanmedia

3. Our Services
Web Design
Internet Marketing
Website Management

```html
<!DOCTYPE html>
<html lang="en">
<head>
<meta charset="utf-8">
<title>Trelvan Media — Business Card</title>
<link rel="stylesheet" href="https://fonts.googleapis.com/css2?family=Open+Sans:wght@400;600;700&display=swap">
<style>
  :root {
    --brand-blue: #1b78b8;
    --brand-blue-dark: #14649c;
    --brand-orange: #f07c22;
    --ink: #2f2f2f;
    --ink-soft: #6b6b6b;
    --card: #ffffff;
    --backdrop: #e9eaec;
  }
  * { box-sizing: border-box; margin: 0; padding: 0; }
  html, body {
    width: 1200px; height: 951px; overflow: hidden;
    background: var(--backdrop);
    font-family: "Open Sans", Arial, sans-serif;
    color: var(--ink);
  }
  .canvas { position: relative; width: 1200px; height: 951px; }

  .card {
    position: absolute;
    width: 600px; height: 343px;
    background: var(--card);
    border-radius: 22px;
    overflow: hidden;
    box-shadow: 0 10px 30px rgba(0,0,0,.18);
  }

  /* Front */
  .card-front { left: 60px; top: 60px; }
  .brand {
    position: absolute; left: 0; right: 0; top: 92px;
    text-align: center;
  }
  .brand-name {
    display: inline-flex; align-items: center; gap: 14px;
    font-weight: 700; font-size: 52px; color: var(--brand-blue);
    letter-spacing: -0.5px; line-height: 1;
  }
  .brand-dot {
    width: 26px; height: 26px; border-radius: 50%;
    background: var(--brand-orange);
  }
  .brand-tagline {
    margin-top: 8px; font-size: 17px; color: var(--ink-soft);
    font-weight: 400;
  }
  .front-url {
    position: absolute; left: 0; right: 0; bottom: 50px;
    text-align: center; font-size: 15px; font-weight: 600;
    letter-spacing: 0.5px; color: var(--ink);
  }
  .service-band {
    position: absolute; left: 0; right: 0; bottom: 0; height: 38px;
    background: var(--brand-blue);
    border-top: 3px solid var(--brand-blue-dark);
    color: #fff; font-size: 14px; font-weight: 600; letter-spacing: .4px;
    display: flex; align-items: center; justify-content: center; gap: 8px;
  }
  .service-band .sep { font-size: 10px; }

  /* Back */
  .card-back { left: 540px; top: 500px; }
  .back-wave { position: absolute; inset: 0; }
  .back-brand { position: absolute; left: 30px; top: 30px; }
  .back-brand .brand-name { font-size: 34px; gap: 10px; }
  .back-brand .brand-dot { width: 18px; height: 18px; }
  .back-brand .brand-tagline { font-size: 12px; margin-top: 4px; padding-left: 28px; }

  .contact-list {
    position: absolute; left: 30px; top: 138px;
    list-style: none; font-size: 13.5px; line-height: 1.35;
  }
  .contact-list li { display: flex; align-items: flex-start; gap: 9px; }
  .contact-list svg { flex: none; width: 13px; height: 13px; margin-top: 3px; fill: var(--brand-blue); }
  .contact-list .hl { color: var(--brand-orange); }
  .social-dot { flex: none; width: 12px; height: 12px; margin-top: 3px; border-radius: 50%; background: var(--brand-blue); }

  .person {
    position: absolute; right: 34px; top: 214px; text-align: right; color: #fff;
  }
  .person-name { font-size: 23px; font-weight: 400; }
  .person-title { font-size: 14px; margin-top: 2px; }
</style>
</head>
<body>
<main class="canvas">

  <section class="card card-front" aria-label="Card front">
    <div class="brand">
      <div class="brand-name"><span class="brand-dot"></span>Trelvan Media</div>
      <div class="brand-tagline">Sites That Perform</div>
    </div>
    <div class="front-url">www.trelvanmedia.example</div>
    <div class="service-band">
      <span>Web Design</span><span class="sep">•</span>
      <span>Internet Marketing</span><span class="sep">•</span>
      <span>Website Management</span>
    </div>
  </section>

  <section class="card card-back" aria-label="Card back">
    <svg class="back-wave" viewBox="0 0 600 343" preserveAspectRatio="none" aria-hidden="true">
      <path d="M392 0 C 440 80, 330 170, 380 343 L600 343 L600 0 Z" fill="var(--brand-orange)"/>
      <path d="M420 0 C 468 80, 358 170, 408 343 L600 343 L600 0 Z" fill="var(--brand-blue)"/>
    </svg>

    <div class="back-brand">
      <div class="brand-name"><span class="brand-dot"></span>Trelvan Media</div>
      <div class="brand-tagline">Sites That Perform</div>
    </div>

    <ul class="contact-list">
      <li><svg viewBox="0 0 16 16"><path d="M1 3h14v10H1z M2 4l6 5 6-5" fill="none" stroke="var(--brand-blue)" stroke-width="1.6"/></svg>mark@trelvanmedia.example</li>
      <li><svg viewBox="0 0 16 16"><path d="M4 1l3 3-2 2c1 2 3 4 5 5l2-2 3 3-2 3C7 14 2 9 1 3z"/></svg>520-381-7459</li>
      <li><svg viewBox="0 0 16 16"><path d="M4 1l3 3-2 2c1 2 3 4 5 5l2-2 3 3-2 3C7 14 2 9 1 3z"/></svg>866-381-7459 (toll free)</li>
      <li><span class="social-dot"></span>@trelvanmedia</li>
      <li><span class="social-dot"></span><span>www.<span class="hl">socialpage.example</span>/trelvanmedia</span></li>
      <li><svg viewBox="0 0 16 16"><path d="M8 1l7 7h-2v7H9v-4H7v4H3V8H1z"/></svg><span>4315 W. Calloway Ave. Ste. 140<br>Tucson, AZ 85792</span></li>
    </ul>

    <div class="person">
      <div class="person-name">Mark Lenner</div>
      <div class="person-title">President/CEO</div>
    </div>
  </section>

</main>
</body>
</html>
```